Velk Partners Building Business Cards

We need a business card that reflects our business as "Solar Experts" in San Diego. Browse our website www.velkpartners.example our License needs to be displayed as "CSLB# 3867140" our phone number is (619) 555-0187

Save thousands on your electric bills and increase the value of your home while helping to protect the environment. Our solar installation experts will help you design the system that's right for you, using only the highest quality equipment that will look great and give you ideal performance. Our goal is to make you energy independent, and get your electric bill to 0.

Paul Osterby
(619) 555-0187
paul@velkpartners.example

Target Market(s)

Home owners in san diego looking for solar

Industry/Entity Type

Solar Energy

Contact Information for Business Card

Paul Osterby
(619) 555-0187
paul@velkpartners.example

Font styles to use
Other font styles liked:
• Use our logo font

Requirements
Must have
• License needs to be displayed as "CSLB# 3867140" our phone number is (619) 555-0187
Nice to have
• Real images of rooftop home solar in san diego
Should not have
• our business address

```html
<!DOCTYPE html>
<html lang="en">
<head>
<meta charset="utf-8">
<title>Velk Partners Building – Business Card</title>
<link rel="stylesheet" href="https://fonts.googleapis.com/css2?family=Open+Sans:ital,wght@0,400;0,600;0,700;1,400&display=swap">
<style>
  :root {
    --navy: #1b3f7a;
    --amber: #f7ae00;
    --amber-light: #fbd775;
    --white: #ffffff;
    --ink: #3c3c3c;
    --stage: #4a4a4a;
  }
  * { box-sizing: border-box; margin: 0; padding: 0; }
  html, body {
    width: 1105px; height: 1200px; overflow: hidden;
    background: var(--stage);
    font-family: "Open Sans", Arial, sans-serif;
  }
  .card {
    position: absolute; left: 193px; width: 718px; height: 410px;
    border-radius: 24px; overflow: hidden;
  }
  .card--front { top: 167px; background: var(--white); }
  .card--back { top: 624px; background: var(--navy); }

  .brand-area {
    position: absolute; left: 330px; right: 0; top: 30px; bottom: 0;
    border-top-left-radius: 260px 270px;
    background: linear-gradient(165deg, var(--amber-light) 0%, var(--amber) 48%, var(--navy) 78%, var(--navy) 100%);
  }
  .brand-name {
    position: absolute; left: 45px; top: 56px;
    font-weight: 700; font-size: 30px; letter-spacing: -0.5px; line-height: 1.2;
    color: var(--navy); white-space: nowrap;
  }
  .person-name {
    position: absolute; left: 45px; top: 183px;
    font-weight: 600; font-size: 25px; line-height: 1.2; color: var(--navy);
  }
  .person-title {
    position: absolute; left: 45px; top: 219px;
    font-size: 19px; line-height: 1.2; color: var(--amber);
  }
  .license {
    position: absolute; left: 45px; top: 256px;
    font-size: 17px; line-height: 1.2; color: var(--ink);
  }
  .contact {
    position: absolute; left: 45px; top: 296px; list-style: none;
    font-size: 17px; color: var(--ink);
  }
  .contact li { display: flex; align-items: center; height: 28px; white-space: nowrap; }
  .contact svg { width: 15px; height: 15px; margin-right: 10px; flex: none; }
  .icon-fill { fill: var(--navy); }

  .back-brand {
    position: absolute; left: 0; right: 0; top: 160px;
    display: flex; justify-content: center; align-items: center; gap: 16px;
  }
  .back-brand .dot {
    width: 40px; height: 40px; border-radius: 50%; background: var(--amber);
  }
  .back-brand .name {
    font-weight: 700; font-size: 34px; color: var(--white); white-space: nowrap;
  }
  .back-web {
    position: absolute; left: 0; right: 0; top: 344px; text-align: center;
    font-style: italic; font-size: 19px; letter-spacing: 4px; color: var(--white);
  }
</style>
</head>
<body>
  <section class="card card--front">
    <div class="brand-area" role="img" aria-label="Brand decoration area in amber and navy"></div>
    <div class="brand-name">Velk Partners Building</div>
    <div class="person-name">Paul Osterby</div>
    <div class="person-title">CEO/Founder</div>
    <div class="license">CSLB# 3867140</div>
    <ul class="contact">
      <li>
        <svg viewBox="0 0 24 24" aria-hidden="true"><path class="icon-fill" d="M6.6 10.8c1.4 2.8 3.8 5.2 6.6 6.6l2.2-2.2c.3-.3.7-.4 1-.2 1.1.4 2.3.6 3.6.6.6 0 1 .4 1 1V20c0 .6-.4 1-1 1C10.6 21 3 13.4 3 4c0-.6.4-1 1-1h3.5c.6 0 1 .4 1 1 0 1.3.2 2.5.6 3.6.1.3 0 .7-.2 1l-2.3 2.2z"/></svg>
        (619) 555-0187
      </li>
      <li>
        <svg viewBox="0 0 24 24" aria-hidden="true"><rect class="icon-fill" x="2" y="5" width="20" height="14" rx="1"/><path d="M3 6l9 7 9-7" fill="none" stroke="#fff" stroke-width="2"/></svg>
        paul@velkpartners.example
      </li>
      <li>
        <svg viewBox="0 0 24 24" aria-hidden="true"><circle class="icon-fill" cx="12" cy="12" r="10"/></svg>
        www.velkpartners.example
      </li>
    </ul>
  </section>

  <section class="card card--back">
    <div class="back-brand">
      <span class="dot"></span>
      <span class="name">Velk Partners Building</span>
    </div>
    <div class="back-web">www.velkpartners.example</div>
  </section>
</body>
</html>
```